BildeVOLD buisnesscard

Hey :) I need a modern buisnesscard for my company BildeVOLD
It most have:
Dagligleder og Fotograf: Henrik Audun Strandvik

Mob: +4791264085
Epost: post@bildevold.example
Adresse: Kvernbakken9, 6040 Fjordvika

Facbook and instagram logo with text BildeVOLD

BildeVOLD logo

It Company

```html
<!DOCTYPE html>
<html lang="no">
<head>
<meta charset="utf-8">
<title>BildeVOLD – visittkort</title>
<link href="https://fonts.googleapis.com/css2?family=Noto+Sans:wght@400;700&display=swap" rel="stylesheet">
<style>
  :root{
    --page:#d9d9d9;
    --card-dark:#252525;
    --card-light:#f2f2f2;
    --brand-grey:#a3a3a3;
    --band:#a0a0a0;
    --band-fold:#7c7c7c;
    --ink:#1e1e1e;
    --white:#ffffff;
  }
  html,body{margin:0;padding:0;overflow:hidden;}
  body{width:1200px;height:1200px;background:var(--page);font-family:"Noto Sans",sans-serif;position:relative;}
  .card{position:absolute;width:720px;height:435px;background:var(--card-dark);overflow:hidden;box-shadow:0 6px 18px rgba(0,0,0,.25);}
  .card--front{left:240px;top:106px;}
  .card--back{left:239px;top:624px;}
  .card__shape{position:absolute;inset:0;}
  .brand-name{position:absolute;color:var(--brand-grey);font-weight:700;white-space:nowrap;transform:translateX(-50%);margin:0;}
  .card--front .brand-name{left:182px;top:196px;font-size:44px;}
  .card--back .brand-name{left:360px;top:170px;font-size:72px;}
  .name-band{position:absolute;left:374px;top:104px;width:346px;height:46px;background:var(--band);}
  .name-band__text{position:absolute;left:22px;top:6px;color:var(--white);font-size:24px;margin:0;white-space:nowrap;}
  .job-title{position:absolute;right:30px;top:170px;font-size:16px;color:var(--ink);margin:0;}
  .contact{position:absolute;right:76px;font-size:19px;color:var(--ink);white-space:nowrap;line-height:1;}
  .contact-icon{position:absolute;left:662px;width:28px;height:28px;}
  .social{position:absolute;top:334px;left:0;width:720px;display:flex;justify-content:center;gap:24px;}
  .social__item{display:flex;align-items:center;gap:10px;color:var(--brand-grey);font-size:19px;}
  .social__dot{width:28px;height:28px;border:2px solid var(--brand-grey);border-radius:50%;box-sizing:border-box;}
</style>
</head>
<body>

<section class="card card--front" aria-label="Visittkort forside">
  <svg class="card__shape" viewBox="0 0 720 435" aria-hidden="true">
    <polygon points="512,0 720,0 720,435 290,435" fill="var(--card-light)"/>
    <polygon points="374,150 424,150 404,213" fill="var(--band-fold)"/>
  </svg>
  <p class="brand-name">BildeVOLD</p>

  <div class="name-band"><p class="name-band__text">Henrik Audun Strandvik</p></div>
  <p class="job-title">Dagligleder og Fotograf</p>

  <span class="contact" style="top:244px">479 126 4085</span>
  <span class="contact" style="top:290px">www.bildevold.example</span>
  <span class="contact" style="top:331px">post@bildevold.example</span>
  <span class="contact" style="top:378px">Kvernbakken9, 6040 Fjordvika</span>

  <svg class="contact-icon" style="top:240px" viewBox="0 0 28 28" aria-hidden="true">
    <circle cx="14" cy="14" r="14" fill="var(--brand-grey)"/>
    <path d="M9 7c1-1 2-1 3 0l1.5 2.5c.5 1 0 1.8-.8 2.3 .8 2 2.3 3.5 4.3 4.3.5-.8 1.3-1.3 2.3-.8L21.8 17c1 1 1 2 0 3-2 2-5 1-8-2s-5-7-4.8-11z" fill="var(--card-light)"/>
  </svg>
  <svg class="contact-icon" style="top:286px" viewBox="0 0 28 28" aria-hidden="true">
    <circle cx="14" cy="14" r="14" fill="var(--brand-grey)"/>
    <circle cx="14" cy="14" r="8" fill="none" stroke="var(--card-light)" stroke-width="1.6"/>
    <path d="M6 14h16M14 6c-3 3-3 13 0 16M14 6c3 3 3 13 0 16" fill="none" stroke="var(--card-light)" stroke-width="1.4"/>
  </svg>
  <svg class="contact-icon" style="top:327px" viewBox="0 0 28 28" aria-hidden="true">
    <circle cx="14" cy="14" r="14" fill="var(--brand-grey)"/>
    <rect x="7" y="9" width="14" height="10" fill="var(--card-light)"/>
    <path d="M7 9l7 6 7-6" fill="none" stroke="var(--brand-grey)" stroke-width="1.3"/>
  </svg>
  <svg class="contact-icon" style="top:374px" viewBox="0 0 28 28" aria-hidden="true">
    <circle cx="14" cy="14" r="14" fill="var(--brand-grey)"/>
    <path d="M14 6a5.5 5.5 0 0 0-5.5 5.5C8.5 16 14 22 14 22s5.5-6 5.5-10.5A5.5 5.5 0 0 0 14 6z" fill="var(--card-light)"/>
    <circle cx="14" cy="11.5" r="2" fill="var(--brand-grey)"/>
  </svg>
</section>

<section class="card card--back" aria-label="Visittkort bakside">
  <p class="brand-name">BildeVOLD</p>
  <div class="social">
    <span class="social__item"><span class="social__dot"></span>BildeVOLD</span>
    <span class="social__item"><span class="social__dot"></span>BildeVOLD</span>
  </div>
</section>

</body>
</html>
```